Fern Pantry needs a bottle label design

We need a bottle label design that is clean, simple and fun. The labels will be for different drink products; OAT. MILK. ALMOND MILK. SOY. We imagine our FP logo at the top, then our brand name FERN PANTRY to be positioned above the the product type OAT. MILK. ALMOND MILK. SOY etc. Underneath the product is made in new zealand. At the base is a check box (suggest using hearts) to denote vegan, planet, dairy free, and recycle friendly. At bottom is bottle size eg 1L, 380ml, 250ml. These are the 3 bottle sizes. Our logo is neon green on light grey background. Fern PAntry is white. back label info to be supplied. Sleeve is under the cap and should have a solid colour around neck. Sleeve to be on white background.

Target Market(s)

25-40 - skew female

Font styles to use
Sans Serif

Requirements
Must have
• Fp Logo and fern pantry
Red hearts against the checks: vegan, recycle, dairy free, planet claims
We are using white caps
The sleeve is going from base to under top of the neck of bottle but will not cover the made in New Zealand underneath the product type eg OAT

```html
<!DOCTYPE html>
<html lang="en">
<head>
<meta charset="utf-8">
<title>Fern Pantry – Oat Milk Bottle Label</title>
<link rel="stylesheet" href="https://fonts.googleapis.com/css2?family=Montserrat:wght@500;600;700&family=Questrial&display=swap">
<style>
  :root {
    --stage-dark: #484848;
    --stage-light: #cbcbcb;
    --label-grey: #6b6c6b;
    --label-white: #f3f3f3;
    --label-white-low: #e8e8e8;
    --neon-green: #22e11c;
    --brand-white: #ffffff;
    --gold-dark: #8f6a2c;
    --gold-light: #c79c55;
    --info-grey: #6a6a6a;
    --heart-red: #e3262d;
    --outline-navy: #1f2a38;
    --cap-white: #ffffff;
    --cap-shade: #e2e2e2;
  }
  * { margin: 0; padding: 0; box-sizing: border-box; }
  html, body { width: 1200px; height: 2500px; overflow: hidden; }
  body { position: relative; font-family: "Questrial", sans-serif; }

  .stage { position: absolute; left: 0; width: 1200px; }
  .stage--flat { top: 0; height: 1300px; background: var(--stage-dark); }
  .stage--bottle { top: 1300px; height: 1200px; background: var(--stage-light); }

  .label {
    position: absolute;
    width: 468px; height: 1078px;
    overflow: hidden;
    background: linear-gradient(180deg, var(--label-grey) 0, var(--label-grey) 600px, var(--label-white) 700px, var(--label-white-low) 1078px);
  }
  .stage--flat .label { left: 365px; top: 132px; box-shadow: 0 10px 30px rgba(0,0,0,.45); }
  .stage--bottle .label { left: 359px; top: 160px; transform: scale(0.91); transform-origin: top left; }

  .brand-mark {
    position: absolute; left: 0; width: 100%; top: 92px;
    text-align: center;
    font-family: "Montserrat", sans-serif; font-weight: 700;
    font-size: 150px; line-height: 150px; letter-spacing: 6px;
    color: var(--neon-green);
  }
  .brand-name {
    position: absolute; left: 0; width: 100%; top: 244px;
    text-align: center;
    font-family: "Montserrat", sans-serif; font-weight: 500;
    font-size: 21px; letter-spacing: 7.5px;
    color: var(--brand-white);
  }
  .milk-splash {
    position: absolute; left: 0; top: 228px; width: 100%; height: 470px;
    background:
      radial-gradient(ellipse 60% 30% at 55% 78%, rgba(200,150,70,.35), transparent 70%),
      linear-gradient(180deg, rgba(107,108,107,0) 0, rgba(107,108,107,0) 55%, #dcdcdc 85%, var(--label-white) 100%);
  }
  .product {
    position: absolute; left: 66px;
    font-family: "Montserrat", sans-serif; font-weight: 600;
    font-size: 128px; line-height: 1;
    background: linear-gradient(180deg, var(--gold-dark) 0%, var(--gold-light) 45%, var(--gold-dark) 100%);
    -webkit-background-clip: text; background-clip: text;
    color: transparent;
    transform-origin: left top;
  }
  .product--first { top: 660px; letter-spacing: -2px; }
  .product--second { top: 758px; letter-spacing: -4px; transform: scaleX(0.86); }
  .origin {
    position: absolute; left: 69px; top: 895px;
    font-size: 22px; color: var(--info-grey); letter-spacing: .8px;
  }
  .claims {
    position: absolute; left: 69px; top: 934px;
    display: flex; gap: 10px;
    font-size: 17px; color: var(--info-grey);
    white-space: nowrap;
  }
  .claim { display: flex; align-items: center; gap: 4px; }
  .claim svg { width: 14px; height: 13px; fill: var(--heart-red); flex: none; }
  .size {
    position: absolute; left: 68px; top: 988px;
    font-size: 28px; color: var(--info-grey);
  }

  .bottle-cap {
    position: absolute; left: 487px; top: 60px; width: 175px; height: 95px;
    border-radius: 14px 14px 4px 4px;
    background: linear-gradient(90deg, var(--cap-shade), var(--cap-white) 35%, var(--cap-white) 65%, var(--cap-shade));
  }
  .bottle-outline { position: absolute; left: 0; top: 0; }
</style>
</head>
<body>

<section class="stage stage--flat">
  <div class="label">
    <div class="brand-mark">FP</div>
    <div class="brand-name">FERN PANTRY</div>
    <div class="milk-splash" role="img" aria-label="Milk pouring into a splash with oat flakes and wheat ears"></div>
    <div class="product product--first">OAT</div>
    <div class="product product--second">MILK</div>
    <div class="origin">MADE IN NEW ZEALAND</div>
    <div class="claims">
      <span class="claim"><svg viewBox="0 0 14 13"><path d="M7 12.5 L1.3 6.8 A3.3 3.3 0 0 1 7 2.6 A3.3 3.3 0 0 1 12.7 6.8 Z"/></svg>Vegan</span>
      <span class="claim"><svg viewBox="0 0 14 13"><path d="M7 12.5 L1.3 6.8 A3.3 3.3 0 0 1 7 2.6 A3.3 3.3 0 0 1 12.7 6.8 Z"/></svg>Dairy Free</span>
      <span class="claim"><svg viewBox="0 0 14 13"><path d="M7 12.5 L1.3 6.8 A3.3 3.3 0 0 1 7 2.6 A3.3 3.3 0 0 1 12.7 6.8 Z"/></svg>Recycle</span>
      <span class="claim"><svg viewBox="0 0 14 13"><path d="M7 12.5 L1.3 6.8 A3.3 3.3 0 0 1 7 2.6 A3.3 3.3 0 0 1 12.7 6.8 Z"/></svg>Planet</span>
    </div>
    <div class="size">1L</div>
  </div>
</section>

<section class="stage stage--bottle">
  <div class="bottle-cap" role="img" aria-label="White screw cap"></div>
  <div class="label">
    <div class="brand-mark">FP</div>
    <div class="brand-name">FERN PANTRY</div>
    <div class="milk-splash" role="img" aria-label="Milk pouring into a splash with oat flakes and wheat ears"></div>
    <div class="product product--first">OAT</div>
    <div class="product product--second">MILK</div>
    <div class="origin">MADE IN NEW ZEALAND</div>
    <div class="claims">
      <span class="claim"><svg viewBox="0 0 14 13"><path d="M7 12.5 L1.3 6.8 A3.3 3.3 0 0 1 7 2.6 A3.3 3.3 0 0 1 12.7 6.8 Z"/></svg>Vegan</span>
      <span class="claim"><svg viewBox="0 0 14 13"><path d="M7 12.5 L1.3 6.8 A3.3 3.3 0 0 1 7 2.6 A3.3 3.3 0 0 1 12.7 6.8 Z"/></svg>Dairy Free</span>
      <span class="claim"><svg viewBox="0 0 14 13"><path d="M7 12.5 L1.3 6.8 A3.3 3.3 0 0 1 7 2.6 A3.3 3.3 0 0 1 12.7 6.8 Z"/></svg>Recycle</span>
      <span class="claim"><svg viewBox="0 0 14 13"><path d="M7 12.5 L1.3 6.8 A3.3 3.3 0 0 1 7 2.6 A3.3 3.3 0 0 1 12.7 6.8 Z"/></svg>Planet</span>
    </div>
    <div class="size">1L</div>
  </div>
  <svg class="bottle-outline" width="1200" height="1200" viewBox="0 0 1200 1200" aria-hidden="true">
    <path d="M495 150 L495 230 C490 330 440 380 400 420 C390 440 386 470 386 520 L386 1060 C386 1120 410 1150 460 1150 L690 1150 C720 1150 735 1120 735 1060 L748 620 L752 590 L748 560 L750 520 C752 470 745 440 735 420 C690 370 655 320 655 230 L655 150"
          fill="none" stroke="var(--outline-navy)" stroke-width="3"/>
    <path d="M487 150 L662 150" fill="none" stroke="var(--outline-navy)" stroke-width="3"/>
    <path d="M492 60 Q575 52 655 60" fill="none" stroke="var(--outline-navy)" stroke-width="3"/>
  </svg>
</section>

</body>
</html>
```